Torvane Halbridge

Looking for modern business cards.
Clean contemporary design.
Similar to this.
https://www.plumvexa-search.example/imgres?imgurl=https%3A%2F%2Fimg.quorlint-cdn.example%2Fsleek_dark_metal_card_design_540.jpg&imgrefurl=https%3A%2F%2Fwww.quorlint-prints.example%2Fsleek_dark_metal_card_design-918273645501928374&q=modern%20business%20cards

But I'd like the blue to look metallic.

Business

```html
<!DOCTYPE html>
<html lang="en">
<head>
<meta charset="utf-8">
<title>Torvane Halbridge — Business Card</title>
<link rel="stylesheet" href="https://fonts.googleapis.com/css2?family=Roboto:wght@400;500&family=Roboto+Condensed:wght@500&display=swap">
<style>
  :root {
    --backdrop: #e8e6e3;
    --navy-teal: #23566e;
    --navy-dark: #173d50;
    --navy-light: #3f7891;
    --bright-teal: #279cbc;
    --teal-dark: #1a7896;
    --teal-light: #6cc6df;
    --teal-sheen: #a9e1ef;
    --accent-teal: #3aa3c9;
    --paper: #f3f3f3;
    --white: #ffffff;
  }
  * { margin: 0; padding: 0; box-sizing: border-box; }
  html, body {
    width: 1200px; height: 960px; overflow: hidden;
    background: var(--backdrop);
    font-family: "Roboto", Arial, sans-serif;
  }
  .canvas { position: relative; width: 1200px; height: 960px; }

  .card { position: absolute; width: 600px; height: 343px; overflow: hidden; }
  .card-front { left: 314px; top: 113px; background: var(--paper); }
  .card-back {
    left: 311px; top: 472px;
    background:
      repeating-linear-gradient(90deg, rgba(255,255,255,0.035) 0 1px, rgba(0,0,0,0.03) 1px 3px),
      linear-gradient(120deg,
        var(--teal-dark) 0%,
        var(--bright-teal) 22%,
        var(--teal-light) 40%,
        var(--teal-sheen) 48%,
        var(--bright-teal) 62%,
        var(--teal-dark) 82%,
        var(--bright-teal) 100%);
  }

  .front-shape { position: absolute; inset: 0; }

  .person { position: absolute; left: 31px; top: 111px; color: var(--white); }
  .person-name {
    font-family: "Roboto Condensed", Arial, sans-serif;
    font-weight: 500; font-size: 21px; color: var(--accent-teal);
    letter-spacing: 0.2px; line-height: 1;
  }
  .person-title { font-size: 15px; font-weight: 500; margin-top: 7px; }
  .address { font-size: 14.5px; line-height: 18px; margin-top: 22px; }
  .contacts { list-style: none; margin-top: 11px; font-size: 14.5px; }
  .contacts li { display: flex; align-items: center; height: 19px; }
  .contacts svg { width: 13px; height: 13px; margin-right: 10px; fill: var(--accent-teal); }

  .brand { position: absolute; left: 284px; top: 78px; }
  .brand-row { display: flex; align-items: center; }
  .brand-name {
    font-size: 28px; font-weight: 400; color: var(--navy-teal); letter-spacing: -0.3px;
    line-height: 1;
  }
  .brand-dot {
    width: 9px; height: 9px; border-radius: 50%;
    background: var(--bright-teal); margin-left: 9px;
  }
  .brand-tagline {
    font-size: 6.5px; color: var(--bright-teal); font-weight: 500;
    margin-top: 8px; margin-left: 60px; letter-spacing: 0.3px; white-space: nowrap;
  }

  .back-name {
    position: absolute; left: 0; right: 0; top: 145px; text-align: center;
    color: var(--white); font-size: 36px; font-weight: 400;
  }
  .back-web {
    position: absolute; left: 0; right: 0; top: 299px; text-align: center;
    color: var(--white); font-size: 14px; letter-spacing: 3px;
  }
</style>
</head>
<body>
<main class="canvas">
  <section class="card card-front">
    <svg class="front-shape" viewBox="0 0 600 343" width="600" height="343" aria-hidden="true">
      <defs>
        <linearGradient id="navyMetal" x1="0" y1="0" x2="1" y2="1">
          <stop offset="0" stop-color="var(--navy-dark)"/>
          <stop offset="0.35" stop-color="var(--navy-teal)"/>
          <stop offset="0.5" stop-color="var(--navy-light)"/>
          <stop offset="0.65" stop-color="var(--navy-teal)"/>
          <stop offset="1" stop-color="var(--navy-dark)"/>
        </linearGradient>
        <linearGradient id="tealMetal" x1="0" y1="0" x2="0" y2="1">
          <stop offset="0" stop-color="var(--teal-dark)"/>
          <stop offset="0.45" stop-color="var(--teal-sheen)"/>
          <stop offset="1" stop-color="var(--teal-dark)"/>
        </linearGradient>
      </defs>
      <path fill="url(#navyMetal)" d="M0 0 H261 C210 30 205 100 240 150 C275 200 300 270 262 343 H0 Z"/>
      <path fill="url(#tealMetal)" d="M261 0 C222 25 212 80 226 120 C218 75 230 30 270 0 Z"/>
      <path fill="url(#tealMetal)" d="M272 180 C305 230 300 295 262 343 L268 343 C302 300 310 235 272 180 Z"/>
    </svg>

    <div class="person">
      <p class="person-name">CORIN ASHDALE</p>
      <p class="person-title">CEO/FOUNDER</p>
      <p class="address">4120 Larchmere Row<br>Wendmoor, Kestral 20816</p>
      <ul class="contacts">
        <li><svg viewBox="0 0 16 16"><path d="M3 1l3 3-1.5 2a9 9 0 0 0 5.5 5.5L12 10l3 3-2 2C7 15 1 9 1 3z"/></svg>512 840 3176</li>
        <li><svg viewBox="0 0 16 16"><path d="M4 0h8v16H4z M5.5 2v10h5V2z" fill-rule="evenodd"/></svg>512 907 4451</li>
        <li><svg viewBox="0 0 16 16"><path d="M4 1h8v4H4z M1 6h14v7h-3v2H4v-2H1z M5 11v2h6v-2z"/></svg>512 840 3177</li>
        <li><svg viewBox="0 0 16 16"><path d="M1 3h14v10H1z M2 4l6 5 6-5v-.5H2z" fill-rule="evenodd"/></svg>corin@torvane.example</li>
        <li><svg viewBox="0 0 16 16"><circle cx="8" cy="8" r="7"/></svg>www.torvane.example</li>
      </ul>
    </div>

    <div class="brand">
      <div class="brand-row">
        <span class="brand-name">Torvane Halbridge</span>
        <span class="brand-dot"></span>
      </div>
      <p class="brand-tagline">"Seasoned leadership for every growing business"</p>
    </div>
  </section>

  <section class="card card-back">
    <p class="back-name">Torvane Halbridge</p>
    <p class="back-web">www.torvane-halbridge.example</p>
  </section>
</main>
</body>
</html>
```